International sourcing and trading company needs website design on Squarespace

We are international sourcing and trading company based in Brisbane ,Australia. We help our clients to source any products they need to economically produce overseas and we manage the whole production process for them. We want our visual identity to show that we are professional, dynamic, efficient and are able to source any product around the world. Our website will be simply information and advertising website , no ecommerce or any transactions. Please see attached our company logo. We would like our website to have the following sections/pages:

1.Main banner with a simple slogan/sentence to introduce what we do: Let us handle the overseas sourcing and production for you.

2. Post-Covid sourcing and producing management: introducing our competence on managing sourcing and overseas production under the travel restriction and the growing tension on global trading. We will supply the exact wording later on;

3. About us: We are a professional team with mature global sourcing and trading experience. We have branch office in Hong Kong and local resources around all areas in China , India and other Asian countries. Our working flow is: received inquiry->start sourcing->(in 1 week time)give price and delivery date on inquired products or further information->(if needed)arrange samples for clients->(if samples and orders are confirmed)deliver Pre-production sample-> kick-off production->arrange inspection through the whole production-> (if need) arrange shipment to client. We would like to show the work flow in a personalized way , eg. personalize icons etc.;

4. What kind of product we can source and produce: our business is sourcing and managing manufacture overseas for our clients, product categories mainly, but not just, are clothing, shoes , bags, clothing accessories, makeup accessories, festival or promotional gifts etc. all kind of daily use products . We basically are able to source and manage production of every kind of products with no limits. We would like this page to be particularly personalized in a way to give impression to whom browse our website feel free to send inquiry of any kind of production to us and they can trust us that we will do our job professionally and dynamically. We are thinking of using some icons of daily use products to show our sourcing category , it's just our though so please feel free to propose any other ides that you think is more suitable from the point of view of professional designer.

5. Start an enquiry: here we need to land on a questionary page to let who would like to make en enquiry leave the main information , including:
-Name & Sir name:
-Company name:
-Contact email:
-Phone numer:
-Enquired product:
-Upload image:
-Preferred or previous production country:
-Preferred price: FOB, CIF, DDP
-If CIF or DDP where the arrival port/airport will be:
-Preferred delivery time:
-Preferred transportation: by air, by sea, by train
- Other specific requires:

6: Contact us: We will supply contact info later on

Above are our thoughts but please feel free to propose any other ideas that you think should be more suitable for us. We trust your expertise and professional opinions.

Wholesalers and retailers who need to produce their products overseas (mainly in China and other countries in Asia)

• We think it will be nice to show information in simple and comprehensive icons instead of piles of words. We will want our website neat, easy to understand what we do and professional. However this is just our thought so please feel free to propose any other ideas that you think is more suitable from the point of view of professional designer.

```html
<!DOCTYPE html>
<html lang="en">
<head>
<meta charset="utf-8">
<title>Orbit Link – Global Sourcing and Production</title>
<link href="https://fonts.googleapis.com/css2?family=Lato:wght@400;700&display=swap" rel="stylesheet">
<style>
:root{
  --orange:#f29b38;
  --teal:#3fa8bf;
  --teal-band:#41a7be;
  --text:#333;
  --light:#f3f3f3;
  --strip:#eeeeee;
  --contact-bg:#e1e7e9;
  --white:#fff;
}
*{margin:0;padding:0;box-sizing:border-box}
html,body{width:1200px;height:3014px;overflow:hidden}
body{font-family:'Lato',sans-serif;color:var(--text);position:relative;background:var(--white)}
.abs{position:absolute}

/* header */
.site-header{position:absolute;left:0;top:0;width:1200px;height:103px;background:var(--white)}
.brand{position:absolute;left:112px;top:36px;display:flex;align-items:center;gap:10px}
.brand-dot{width:22px;height:22px;border-radius:50%;background:var(--teal)}
.brand-name{font-size:28px;font-weight:700;color:var(--orange)}
.main-nav{position:absolute;right:111px;top:46px;display:flex;gap:38px;font-size:14px;font-weight:700;text-transform:uppercase}
.main-nav a{color:#222;text-decoration:none;position:relative}
.main-nav a.active{color:var(--teal);font-weight:400}
.main-nav a.active::after{content:"";position:absolute;left:-2px;right:-2px;top:28px;height:2px;background:var(--teal)}

/* hero */
.hero{position:absolute;left:0;top:103px;width:1200px;height:908px;overflow:hidden}
.hero-photo{position:absolute;inset:0;background:radial-gradient(ellipse at 60% 70%,#f3b45a 0%,#b57a45 22%,#5c5a5c 55%,#3f4652 100%)}
.hero-title{position:absolute;left:0;width:1200px;top:130px;text-align:center;color:var(--white);font-size:51px;font-weight:400;line-height:57px;text-transform:uppercase}
.btn-outline{position:absolute;display:flex;align-items:center;justify-content:center;border:2px solid var(--white);color:var(--white);font-size:18px;text-transform:uppercase;text-decoration:none}
.hero-curve{position:absolute;left:0;top:0}
.covid-title{position:absolute;left:0;width:1200px;top:762px;text-align:center;color:var(--white);font-size:32px;font-weight:700;text-transform:uppercase}
.covid-text{position:absolute;left:200px;width:800px;top:810px;text-align:center;color:var(--white);font-size:16.5px;line-height:24px}

/* about */
.about{position:absolute;left:0;top:1011px;width:1200px;height:660px;background:var(--light)}
.section-title{position:absolute;left:0;width:1200px;text-align:center;font-size:32px;font-weight:700;color:var(--teal);text-transform:uppercase}
.about-text{position:absolute;left:155px;width:890px;top:118px;text-align:center;font-size:16.5px;line-height:24px;color:#222}
.step-label{position:absolute;font-size:13px;line-height:18px;color:#222;width:240px}
.step-label.left{text-align:right}
.step-icon{position:absolute;width:72px;height:72px;border-radius:50%;background:var(--white);box-shadow:0 1px 4px rgba(0,0,0,.12);display:flex;align-items:center;justify-content:center}
.hub-name{font-size:30px;font-weight:700;fill:var(--orange)}

/* products */
.products{position:absolute;left:0;top:1671px;width:1200px;height:619px;overflow:hidden}
.products-photo{position:absolute;inset:0;background:linear-gradient(180deg,#46adc2 0%,#3ea3b9 55%,#5cb3c5 100%)}
.category-tabs{position:absolute;left:111px;top:132px;width:978px;height:42px;background:var(--white);display:flex;font-size:15.5px;text-transform:uppercase}
.category-tabs span{display:flex;align-items:center;padding:0 16px;color:#222}
.category-tabs span.active{background:var(--orange);color:#333}
.product-card{position:absolute;top:214px;width:305px;height:248px}
.product-photo{height:208px;background:linear-gradient(180deg,#e4e2dd,#d9d6d0)}
.product-name{height:40px;background:var(--orange);color:var(--white);display:flex;align-items:center;justify-content:center;font-size:15.5px;text-transform:uppercase}
.btn-view{font-weight:700;font-size:15.5px}

/* enquiry strip */
.enquiry-strip{position:absolute;left:0;top:2290px;width:1200px;height:140px;background:var(--strip)}
.enquiry-text{position:absolute;left:111px;top:54px;width:790px;font-size:20px;line-height:24px;color:var(--teal);text-transform:uppercase}
.btn-solid{position:absolute;background:var(--orange);color:var(--white);display:flex;align-items:center;justify-content:center;font-weight:700;font-size:16px;text-transform:uppercase;text-decoration:none}

/* contact */
.contact{position:absolute;left:0;top:2430px;width:1200px;height:524px;background:var(--contact-bg)}
.contact-line{position:absolute;left:111px;display:flex;gap:10px;font-size:16.5px;line-height:23px;color:#222}
.social{position:absolute;top:2802px;width:38px;height:38px;border-radius:50%;background:var(--orange)}
.field{position:absolute;background:var(--white);border:1px solid #d4d8da;font-size:15px;color:#666;padding:10px 12px}

.site-footer{position:absolute;left:0;top:2954px;width:1200px;height:60px;background:var(--teal);color:var(--white);font-size:13px;display:flex;align-items:center;justify-content:center}
</style>
</head>
<body>

<header class="site-header">
  <div class="brand"><span class="brand-dot"></span><span class="brand-name">Orbit Link</span></div>
  <nav class="main-nav">
    <a class="active" href="#">Home</a>
    <a href="#">About us</a>
    <a href="#">What we do</a>
    <a href="#">Source and produce</a>
    <a href="#">Blog</a>
    <a href="#">Contact us</a>
  </nav>
</header>

<section class="hero">
  <div class="hero-photo" role="img" aria-label="Silhouettes of two business partners shaking hands in front of a world map and city skyline at sunset"></div>
  <h1 class="hero-title">Let us handle the overseas sourcing<br>and production for you</h1>
  <a class="btn-outline" href="#" style="left:522px;top:263px;width:155px;height:52px">Contact us</a>
  <svg class="hero-curve" width="1200" height="908" viewBox="0 0 1200 908">
    <path d="M0 424 C300 560 700 690 1200 700 L1200 908 L0 908 Z" fill="var(--teal-band)"/>
    <path d="M0 466 C300 590 700 716 1200 727 L1200 908 L0 908 Z" fill="var(--orange)" fill-opacity=".92"/>
  </svg>
  <h2 class="covid-title">Post-Covid sourcing and producing management</h2>
  <p class="covid-text">Introducing our competence on managing sourcing and overseas production under the travel restriction and the growing tension on global trading</p>
</section>

<section class="about">
  <h2 class="section-title" style="top:62px">About us</h2>
  <p class="about-text">We are a professional team with mature global sourcing and trading experience. We have branch office in Hong Kong and local resources around all areas in China , India and other Asian countries</p>

  <svg class="abs" style="left:0;top:0" width="1200" height="660" viewBox="0 0 1200 660">
    <g stroke="#9a9a9a" stroke-width="1" fill="none">
      <path d="M403 261 H504 V544 H403"/>
      <path d="M403 356 H504 M403 450 H504"/>
      <path d="M797 261 H697 V544 H797"/>
      <path d="M797 356 H697 M797 450 H697"/>
    </g>
    <circle cx="600" cy="405" r="146" fill="var(--orange)"/>
    <circle cx="600" cy="405" r="116" fill="var(--white)"/>
    <text x="600" y="415" text-anchor="middle" class="hub-name">Orbit Link</text>
  </svg>

  <!-- left steps -->
  <p class="step-label left" style="left:85px;top:252px">Received inquiry</p>
  <div class="step-icon" style="left:331px;top:225px"><svg width="34" height="34" viewBox="0 0 34 34" fill="none" stroke="var(--teal)" stroke-width="1.6"><rect x="8" y="4" width="18" height="22" rx="2"/><path d="M12 11h10M12 16h10M12 21h6"/><path d="M4 30h26"/></svg></div>

  <p class="step-label left" style="left:85px;top:347px">Start sourcing</p>
  <div class="step-icon" style="left:331px;top:320px"><svg width="34" height="34" viewBox="0 0 34 34" fill="none" stroke="var(--teal)" stroke-width="1.6"><path d="M3 6h5l4 16h15l3-11H10"/><circle cx="14" cy="28" r="2"/><circle cx="25" cy="28" r="2"/></svg></div>

  <p class="step-label left" style="left:85px;top:423px">(In 1 week time)give price and delivery date on inquired products or further information</p>
  <div class="step-icon" style="left:331px;top:414px"><svg width="34" height="34" viewBox="0 0 34 34" fill="none" stroke="var(--teal)" stroke-width="1.6"><rect x="8" y="4" width="20" height="26" rx="2"/><path d="M12 9h12M12 15h4M20 15h4M12 20h4M20 20h4M12 25h4M20 25h4"/></svg></div>

  <p class="step-label left" style="left:85px;top:535px">(If needed)arrange samples for clients</p>
  <div class="step-icon" style="left:331px;top:508px"><svg width="34" height="34" viewBox="0 0 34 34" fill="none" stroke="var(--teal)" stroke-width="1.6"><rect x="5" y="5" width="11" height="11"/><rect x="18" y="18" width="11" height="11"/><path d="M22 6a6 6 0 0 1 6 6M12 28a6 6 0 0 1-6-6"/></svg></div>

  <!-- right steps -->
  <div class="step-icon" style="left:797px;top:225px"><svg width="34" height="34" viewBox="0 0 34 34" fill="none" stroke="var(--teal)" stroke-width="1.6"><rect x="4" y="5" width="26" height="18" rx="1"/><path d="M13 28h8M17 23v5M9 11h8M9 16h14"/></svg></div>
  <p class="step-label" style="left:876px;top:232px;width:200px">(if samples and orders are confirmed)deliver Pre-production sample</p>

  <div class="step-icon" style="left:797px;top:320px"><svg width="34" height="34" viewBox="0 0 34 34" fill="none" stroke="var(--teal)" stroke-width="1.6"><circle cx="17" cy="17" r="5"/><circle cx="17" cy="17" r="10"/><path d="M17 3v4M17 27v4M3 17h4M27 17h4M7 7l3 3M24 24l3 3M27 7l-3 3M7 27l3-3"/></svg></div>
  <p class="step-label" style="left:876px;top:347px">Kick-off production</p>

  <div class="step-icon" style="left:797px;top:414px"><svg width="34" height="34" viewBox="0 0 34 34" fill="none" stroke="var(--teal)" stroke-width="1.6"><path d="M17 4l12 6-12 6-12-6z"/><path d="M5 17l12 6 12-6M5 24l12 6 12-6"/></svg></div>
  <p class="step-label" style="left:876px;top:441px;width:220px">Arrange inspection through the whole production</p>

  <div class="step-icon" style="left:797px;top:508px"><svg width="34" height="34" viewBox="0 0 34 34" fill="none" stroke="var(--teal)" stroke-width="1.6"><path d="M6 10h16v14H6zM22 14h6l3 4v6h-9"/><circle cx="11" cy="26" r="2.5"/><circle cx="26" cy="26" r="2.5"/><path d="M2 14h6M1 18h6"/></svg></div>
  <p class="step-label" style="left:876px;top:535px">(if need) arrange shipment to client</p>
</section>

<section class="products">
  <div class="products-photo" role="img" aria-label="Container port with stacked shipping containers and cranes, tinted teal"></div>
  <h2 class="section-title" style="top:62px;color:var(--white)">Product categories</h2>
  <div class="category-tabs">
    <span class="active">Clothing</span><span>Shoes</span><span>Bags</span><span>Clothing accessories</span><span>Makeup accessories</span><span>Festival or promotional gifts</span>
  </div>
  <div class="product-card" style="left:111px"><div class="product-photo" role="img" aria-label="Dark patterned long-sleeve blouse"></div><div class="product-name">Nostrum exercitationem</div></div>
  <div class="product-card" style="left:448px"><div class="product-photo" role="img" aria-label="Black blouse with tie neck"></div><div class="product-name">Occaecat cupidatat</div></div>
  <div class="product-card" style="left:785px"><div class="product-photo" role="img" aria-label="Magenta patterned shirt dress"></div><div class="product-name">Necessitatibus saepe</div></div>
  <a class="btn-outline btn-view" href="#" style="left:522px;top:517px;width:157px;height:47px">View more</a>
</section>

<section class="enquiry-strip">
  <p class="enquiry-text">Here we need to land on a questionary page to let who would like to make en enquiry leave the main information</p>
  <a class="btn-solid" href="#" style="left:910px;top:46px;width:178px;height:54px">Start an enquiry</a>
</section>

<section class="contact">
  <h2 class="section-title" style="top:70px">Contact us</h2>
  <div class="contact-line" style="top:169px">
    <svg width="14" height="18" viewBox="0 0 14 18"><path d="M7 0a7 7 0 0 1 7 7c0 5-7 11-7 11S0 12 0 7a7 7 0 0 1 7-7z" fill="var(--orange)"/><circle cx="7" cy="7" r="2.5" fill="var(--contact-bg)"/></svg>
    <span>Orbit Link<br>1000 &nbsp;Street Address#402<br>City Name, Country Code</span>
  </div>
  <div class="contact-line" style="top:257px">
    <svg width="14" height="18" viewBox="0 0 16 16"><path d="M3 1l3 3-2 2c1 2 3 4 5 5l2-2 3 3-2 3C7 15 1 9 0 3z" fill="var(--orange)"/></svg>
    <span>001-23456-78901</span>
  </div>
  <div class="contact-line" style="top:305px">
    <svg width="17" height="18" viewBox="0 0 17 14"><rect y="1" width="17" height="12" fill="var(--orange)"/><path d="M0 1l8.5 6L17 1" stroke="var(--contact-bg)" stroke-width="1.5" fill="none"/></svg>
    <span>inquiries@domainname.com</span>
  </div>
  <span class="social" style="left:111px;top:372px"></span>
  <span class="social" style="left:158px;top:372px"></span>

  <div class="field" style="left:496px;top:166px;width:291px;height:40px">Your name</div>
  <div class="field" style="left:796px;top:166px;width:292px;height:40px">Phone number</div>
  <div class="field" style="left:496px;top:226px;width:592px;height:40px">Email</div>
  <div class="field" style="left:496px;top:287px;width:592px;height:90px">Your message</div>
  <a class="btn-solid" href="#" style="left:496px;top:397px;width:146px;height:48px">Submit now</a>
</section>

<footer class="site-footer">Copyrights © 2020 Orbit Link. &nbsp;All rights reserved.</footer>

</body>
</html>
```